Chocolate Chip Cupcake package design

The cake is a branded packaged cupcake with chocolate chips on top and moist vanilla cake.

Our company is a baking company based in Middle East, producing high quality, European standard food snacks at an affordable price. We want a Clean, Modern and Trendy design - not too cluttered, colored yet not very busy, with a cupcake image (See attached for reference images).

Attached is Brindle Cupcake image - we feel it is clean but classic (we would like something more modern - this image is for your reference only, not as a guideline).

The Front side is 90 x 70mm. It will be a metallic packaging.

Target Market(s)

Teenagers, Adults - Lower, Middle and Upper Middle Class

Industry/Entity Type

It Company

Colors

Designer to choose colors to be used in the design.

Requirements
Must have
• Clean and a Modern - Appealing look
• "Choco Chip Cupcake" - product name
• Product photo
Should not have
• Too cluttered, busy background, very playful design.

```html
<!DOCTYPE html>
<html lang="en">
<head>
<meta charset="utf-8">
<title>Choco Chip Cupcake – Pouch Front</title>
<link rel="stylesheet" href="https://fonts.googleapis.com/css2?family=Patrick+Hand&family=Patrick+Hand+SC&display=swap">
<style>
  :root {
    --backdrop: #a9ddd8;
    --pouch: #efe1d6;
    --pouch-shade: #e4d3c6;
    --seal: #211f1d;
    --ink: #2a2623;
    --ink-soft: #4a4440;
    --banner: #8d7a66;
    --banner-text: #efe4d8;
    --chip: #8a6a55;
    --photo-light: #e8e6ea;
    --photo-cake: #d2a864;
  }
  * { box-sizing: border-box; margin: 0; padding: 0; }
  html, body { width: 1200px; height: 720px; overflow: hidden; }
  body {
    background: var(--backdrop);
    font-family: "Patrick Hand", "Comic Sans MS", cursive;
    display: flex;
    align-items: center;
    justify-content: center;
  }
  .pouch-front {
    position: relative;
    width: 440px;
    height: 660px;
    background: linear-gradient(180deg, var(--pouch) 0%, var(--pouch) 70%, var(--pouch-shade) 100%);
    overflow: hidden;
  }
  .seal-band {
    position: absolute;
    top: 0; left: 0; right: 0;
    height: 84px;
    background: var(--seal);
  }
  .product-name {
    position: absolute;
    top: 152px;
    left: 0; right: 0;
    text-align: center;
    color: var(--ink);
  }
  .product-name .flavour {
    display: block;
    font-family: "Patrick Hand SC", "Patrick Hand", cursive;
    font-size: 26px;
    letter-spacing: 1px;
    color: var(--ink-soft);
    line-height: 1;
  }
  .product-name .item {
    display: block;
    font-family: "Patrick Hand SC", "Patrick Hand", cursive;
    font-size: 64px;
    font-weight: 400;
    letter-spacing: 1px;
    line-height: 1;
    margin-top: 2px;
    -webkit-text-stroke: 1.4px var(--ink);
  }
  .tagline {
    position: absolute;
    top: 250px;
    left: 50%;
    transform: translateX(-50%);
    background: var(--banner);
    color: var(--banner-text);
    font-size: 15px;
    letter-spacing: 0.5px;
    padding: 1px 6px;
    white-space: nowrap;
  }
  .product-photo {
    position: absolute;
    left: 110px;
    top: 370px;
    width: 228px;
    height: 228px;
    border-radius: 50%;
    background: radial-gradient(circle at 60% 45%, var(--photo-cake) 0%, #c9a06a 35%, #b9b6c0 65%, var(--photo-light) 100%);
  }
  .chip-scatter {
    position: absolute;
    left: 40px;
    top: 520px;
    width: 200px;
    height: 130px;
    background: radial-gradient(ellipse at 40% 50%, rgba(138,106,85,0.35) 0%, rgba(138,106,85,0) 70%);
  }
  .net-weight {
    position: absolute;
    right: 30px;
    bottom: 40px;
    font-size: 22px;
    color: #6e645c;
    letter-spacing: 1px;
  }
</style>
</head>
<body>
  <main class="pouch-front">
    <div class="seal-band"></div>
    <h1 class="product-name">
      <span class="flavour">CHOCO CHIP</span>
      <span class="item">CUPCAKE</span>
    </h1>
    <p class="tagline">TEXT TEXT TEXT TEXT TEXT</p>
    <div class="chip-scatter" role="img" aria-label="Scattered chocolate chip decoration"></div>
    <div class="product-photo" role="img" aria-label="Photo of chocolate chip cupcakes on a white cloth"></div>
    <p class="net-weight">900 G</p>
  </main>
</body>
</html>
```